Recruitment of Archipel Manpower for the UK market

I want a website for the UK market to attract businesses and companies to come to us for Philipine labour. We want an information site that gives all information on what we do and how we can recruit Philippine labour.
This is a recruitment site for companies to contact us with their requirements for skilled workers coming from the Philipines over to the UK to work.

Target Market(s)

Uk Companies and businesses who want Philipine skilled workers

Industry/Entity Type

REcruitment

Coding

Number of Pages Required

5+ page

Font styles to use
Sans Serif

Colors
0054AA
0677BA
7BADD7
CADEEF
E8F1F8
0094D4
00A9DD
6FCCEA
C7EBF8
E9F6FB
EE7325
F08F49
F5BC92
FAE3D3
FDF4ED
EB3D1F
EC4F4E
F09395
F8D3D4
FCEDEE

Requirements
Must have
• Look professional and corperate with drop down menus for Home ,about, services,articles. training , contact us
Nice to have
• Look at Velmora recruitment- https://velmorarecruitment.example.co.uk/. This is my current site - https://www.trellanstaffing.example.com/
Should not have
• Cartoons or silly pictures , needs to be corperate looking

```html
<!DOCTYPE html>
<html lang="en">
<head>
<meta charset="utf-8">
<title>Archipel Manpower – Skilled Philippine Workers for UK Companies</title>
<link rel="stylesheet" href="https://fonts.googleapis.com/css2?family=Roboto+Condensed:ital,wght@1,700&family=Poppins:wght@400;500;600&display=swap">
<style>
:root{
  --red:#EB3D1F;
  --orange:#EE7325;
  --blue:#0054AA;
  --ink:#1c1c1c;
  --text:#555;
  --muted:#8a8a8a;
  --soft:#f8f8f9;
  --line:#d9d9d9;
  --map:#e4e4e6;
  --white:#fff;
}
*{box-sizing:border-box;margin:0;padding:0}
html,body{width:1200px;height:4528px;overflow:hidden}
body{font-family:"Poppins",sans-serif;color:var(--text);background:var(--white);position:relative}
.abs{position:absolute}
.title{font-family:"Roboto Condensed",sans-serif;font-style:italic;font-weight:700;color:var(--ink)}
.accent{color:var(--red)}

/* header */
.site-header{position:absolute;left:0;top:0;width:1200px;height:90px;background:var(--white)}
.brand{position:absolute;left:52px;top:28px;font-size:24px;font-weight:600;color:#8b1a1a;letter-spacing:.5px}
.main-nav{position:absolute;left:380px;top:36px;display:flex;gap:30px;font-size:13px;color:#333;text-transform:uppercase}
.main-nav .active{color:var(--red)}
.main-nav .drop::after{content:"";display:inline-block;width:5px;height:5px;border-right:1.5px solid #333;border-bottom:1.5px solid #333;transform:rotate(45deg);margin-left:6px;position:relative;top:-3px}
.phone-tab{position:absolute;left:915px;top:0;width:285px;height:90px;background:var(--red);clip-path:polygon(40px 0,100% 0,100% 100%,0 100%);display:flex;align-items:center;gap:10px;padding-left:48px;color:var(--white);font-size:26px;font-weight:600}

/* hero */
.hero{position:absolute;left:0;top:90px;width:1200px;height:577px;background:linear-gradient(110deg,#3a2f2a 0%,#5a4a40 35%,#2f3a48 70%,#1e2a38 100%)}
.hero-copy{position:absolute;left:124px;top:195px;border-left:3px solid var(--red);padding-left:12px}
.hero-copy h1{font-size:40px;line-height:47px;color:var(--white)}
.hero-copy h1 .accent{color:var(--red)}
.hero-sub{position:absolute;left:124px;top:343px;width:460px;color:var(--white);font-size:15px;line-height:24px}
.btn{display:inline-flex;align-items:center;gap:8px;border-radius:24px;color:var(--white);font-weight:500}
.hero .hero-btn{position:absolute;left:124px;top:415px;height:44px;padding:0 26px;background:var(--red);font-size:14px}
.contact-card{position:absolute;left:738px;top:82px;width:337px;height:413px;background:var(--white);border-top:4px solid var(--red)}
.contact-card h2{position:absolute;left:0;top:22px;width:100%;font-size:27px;line-height:34px;text-align:center}
.field{position:absolute;left:29px;width:279px;height:40px;border:1px solid var(--line);border-radius:3px;display:flex;align-items:center;gap:8px;padding-left:12px;font-size:12px;color:#999;font-style:italic}
.field.message{height:78px;align-items:flex-start;padding-top:10px}
.send-btn{position:absolute;left:29px;top:330px;background:#222;height:46px;padding:0 24px;font-size:14px}

/* about */
.about-collage .ph{position:absolute}
.eyebrow{font-size:12px;letter-spacing:5px;color:#666;text-transform:uppercase}
.rule{width:50px;height:2px;background:var(--red)}
.about-text p{font-size:12.5px;line-height:23px;color:var(--text);margin-bottom:14px;width:377px}
.small-btn{background:var(--red);height:40px;padding:0 26px;font-size:13px}

/* work section */
.work{position:absolute;left:0;top:1280px;width:1200px;height:2110px;background:var(--soft)}
.center-head{position:absolute;left:0;width:1200px;text-align:center}
.center-head .rule{margin:12px auto 0}
.step-num{position:absolute;width:40px;height:40px;border-radius:50%;background:var(--red);color:var(--white);font-weight:600;font-size:20px;display:flex;align-items:center;justify-content:center}
.step-title{position:absolute;font-size:28px}
.step-body{position:absolute;width:340px;font-size:12.5px;line-height:23px}
.frame{position:absolute;width:210px;height:140px;border:7px solid var(--red)}
.frame.tr{border-left:none;border-bottom:none}
.frame.tl{border-right:none;border-bottom:none}

/* centres map area */
.map-area{position:absolute;left:440px;top:3740px;width:320px;height:440px;border-radius:6px;background:linear-gradient(165deg,var(--map) 0%,#ededee 50%,#f4f4f5 100%)}

/* footer */
.site-footer{position:absolute;left:0;top:4190px;width:1200px;height:300px;background:var(--blue);color:var(--white)}
.site-footer h4{font-size:15px;font-weight:500;position:absolute}
.foot-links{position:absolute;font-size:12px;display:grid;grid-template-columns:105px 105px;row-gap:28px}
.foot-links span::before{content:"›";margin-right:8px}
.foot-contact{position:absolute;font-size:12px;line-height:20px}
.foot-contact div{display:flex;gap:12px;margin-bottom:12px}
.social{position:absolute;display:flex;gap:8px}
.social span{width:28px;height:28px;border-radius:50%;border:1.5px solid var(--white)}
.copyright{position:absolute;left:0;top:4490px;width:1200px;height:38px;background:var(--orange);color:var(--white);font-size:12px;display:flex;align-items:center;justify-content:center}
</style>
</head>
<body>

<header class="site-header">
  <div class="brand">Archipel Manpower</div>
  <nav class="main-nav">
    <span class="active">Home</span><span>About</span><span class="drop">Services</span><span>Articles</span><span>Training</span><span>Contact Us</span>
  </nav>
  <div class="phone-tab">
    <svg width="26" height="26" viewBox="0 0 24 24" fill="none" stroke="#fff" stroke-width="2"><path d="M22 16.9v3a2 2 0 0 1-2.2 2 19.8 19.8 0 0 1-8.6-3.1 19.5 19.5 0 0 1-6-6A19.8 19.8 0 0 1 2.1 4.2 2 2 0 0 1 4.1 2h3a2 2 0 0 1 2 1.7c.1 1 .4 1.9.7 2.8a2 2 0 0 1-.5 2.1L8 9.9a16 16 0 0 0 6 6l1.3-1.3a2 2 0 0 1 2.1-.4c.9.3 1.8.6 2.8.7a2 2 0 0 1 1.7 2z"/></svg>
    020 7946 0832
  </div>
</header>

<section class="hero" role="img" aria-label="Photo of smiling office team collaborating at a desk">
  <div class="hero-copy">
    <h1 class="title">Recruiting And Placing<br><span class="accent">Skilled Philippine Workers</span><br>Into UK Companies</h1>
  </div>
  <p class="hero-sub">We source skilled workers directly from the Philippines to work in the UK.</p>
  <span class="btn hero-btn">CONTACT US
    <svg width="16" height="10" viewBox="0 0 16 10" fill="none" stroke="#fff" stroke-width="1.6"><path d="M0 5h15M11 1l4 4-4 4"/></svg></span>
  <form class="contact-card">
    <h2 class="title">Contact Us Today</h2>
    <div class="field" style="top:82px"><svg width="11" height="11" viewBox="0 0 12 12" fill="#bbb"><circle cx="6" cy="3.5" r="3"/><path d="M0 12c0-3.5 2.7-5 6-5s6 1.5 6 5z"/></svg>Name</div>
    <div class="field" style="top:134px"><svg width="12" height="10" viewBox="0 0 12 10" fill="none" stroke="#bbb"><rect x=".5" y=".5" width="11" height="9"/><path d="M.5.5l5.5 5 5.5-5"/></svg>Email</div>
    <div class="field" style="top:186px"><svg width="11" height="11" viewBox="0 0 24 24" fill="#bbb"><path d="M6.6 10.8a15 15 0 0 0 6.6 6.6l2.2-2.2c.3-.3.7-.4 1-.2 1.1.4 2.3.6 3.6.6.6 0 1 .4 1 1V20c0 .6-.4 1-1 1A17 17 0 0 1 3 4c0-.6.4-1 1-1h3.5c.6 0 1 .4 1 1 0 1.3.2 2.5.6 3.6.1.3 0 .7-.2 1z"/></svg>Phone</div>
    <div class="field message" style="top:238px"><svg width="11" height="11" viewBox="0 0 12 12" fill="#bbb"><path d="M0 12l1-4 7-7 3 3-7 7z"/></svg>Message</div>
    <span class="btn send-btn">Send Message
      <svg width="16" height="10" viewBox="0 0 16 10" fill="none" stroke="#fff" stroke-width="1.6"><path d="M0 5h15M11 1l4 4-4 4"/></svg></span>
  </form>
</section>

<section class="about">
  <div class="about-collage">
    <div class="ph" style="left:161px;top:786px;width:225px;height:246px;background:linear-gradient(160deg,#e8e2d8,#c94a4a 60%,#3b3b3b)" role="img" aria-label="Photo of an engineer in a hard hat beside an office worker"></div>
    <div class="ph" style="left:404px;top:757px;width:192px;height:196px;background:linear-gradient(160deg,#d8a070,#5f8fbf 55%,#3d6a9a)" role="img" aria-label="Photo of a group of workers in blue uniforms"></div>
    <div class="ph" style="left:337px;top:971px;width:180px;height:180px;background:linear-gradient(160deg,#c9c9c9,#6b6b6b 50%,#b33a2a)" role="img" aria-label="Photo of two welders in hard hats at work"></div>
    <div class="ph" style="left:178px;top:1050px;width:142px;height:141px;background:linear-gradient(160deg,#f1f1f1,#d8dde6 50%,#7aa6c8)" role="img" aria-label="Photo of a medical team in white coats"></div>
  </div>
  <div class="abs about-text" style="left:660px;top:775px">
    <div class="eyebrow">About</div>
    <h2 class="title" style="font-size:33px;margin-top:12px">Archipel <span class="accent">Manpower</span></h2>
    <div class="rule" style="margin:12px 0 20px"></div>
    <p>We source skilled workers directly from the Philippines to work in the UK. With offices , training locations and specialist recruiters we can find the highest quality individuals to add value and resources to any UK buisness. We delivery quality based on vast experience over a number of years.</p>
    <p>Our company has been estabilished in the Philippines for <b style="color:#222">over 20 years.</b> We have mainly been recruiting philippine workers for the off shore industry in asia but since brexit and the new rules on skilled workers entering the UK we have been working with UK companies.</p>
    <span class="btn small-btn" style="margin-top:10px">Read More
      <svg width="16" height="10" viewBox="0 0 16 10" fill="none" stroke="#fff" stroke-width="1.6"><path d="M0 5h15M11 1l4 4-4 4"/></svg></span>
  </div>
</section>

<section class="work">
  <div class="center-head" style="top:75px">
    <div class="eyebrow">Working Together</div>
    <h2 class="title" style="font-size:34px;margin-top:10px">Archipel Manpower <span class="accent">Recruit</span></h2>
    <div class="rule"></div>
    <p style="font-size:14.5px;color:#222;margin-top:20px">We recruit the finest talent available with our dedicated 200 strong team.</p>
  </div>

  <div class="frame tr" style="left:828px;top:230px"></div>
  <div class="abs" style="left:610px;top:237px;width:420px;height:345px;background:linear-gradient(120deg,#c25a45,#e7e2dc 45%,#cfd4da)" role="img" aria-label="Photo of a recruiter holding a network of candidate profiles"></div>
  <div class="step-num" style="left:161px;top:293px">1</div>
  <h3 class="title step-title" style="left:216px;top:293px">What We Do</h3>
  <p class="step-body" style="left:218px;top:340px">Our company has been estabilished in the Philippines for <b style="color:#222">over 20 years.</b> We have mainly been recruiting philippine workers for the off shore industry in asia but since brexit and the new rules on skilled workers entering the UK we have been working with UK companies who now have chance to recruit some of the finest hard working talent from the Philippines for their companies.</p>

  <div class="frame tl" style="left:161px;top:700px"></div>
  <div class="abs" style="left:168px;top:707px;width:420px;height:344px;background:linear-gradient(150deg,#b9c4a8,#d9d2c2 45%,#ece9e4)" role="img" aria-label="Photo of passport visa stamps and an approved work permit"></div>
  <div class="step-num" style="left:638px;top:766px">2</div>
  <h3 class="title step-title" style="left:693px;top:766px">How We Help</h3>
  <p class="step-body" style="left:696px;top:812px">We work with companies to find skilled workers that meet the UK requirements for Visas and work permits. We guide you through the whole process and deliver highly trained people that add value to your business. We are here to help both the companies and the Philippino people to gain a better standard of living for their families.</p>

  <div class="frame tr" style="left:828px;top:1167px"></div>
  <div class="abs" style="left:610px;top:1174px;width:420px;height:344px;background:linear-gradient(120deg,#cfd3d6,#4a4e55 40%,#8f8a86 75%,#d7d9db)" role="img" aria-label="Photo of business people in a meeting reviewing documents"></div>
  <div class="step-num" style="left:161px;top:1231px">3</div>
  <h3 class="title step-title" style="left:216px;top:1231px">Where To Start</h3>
  <p class="step-body" style="left:218px;top:1278px">We need to know what your issues are and how we can understand the personnal you require , over what time frame and the number of employees you need. Once this is estabilished we start sourcing workers in the Philippines that meet your criteria while starting the process in the UK to be able to have all the documents in place to deliver your company hard working skilled individuals.</p>

  <div class="frame tl" style="left:161px;top:1640px"></div>
  <div class="abs" style="left:168px;top:1647px;width:420px;height:344px;background:linear-gradient(120deg,#c9ccd0,#e9e9ea 40%,#2f3644 80%)" role="img" aria-label="Photo of a businessman shaking hands across a desk"></div>
  <div class="step-num" style="left:638px;top:1704px">4</div>
  <h3 class="title step-title" style="left:693px;top:1704px">Contact Us Today</h3>
  <p class="step-body" style="left:696px;top:1750px">Please contact us today with your requirements , this can be care workers ,chef, welders, pipe fitters, caravan cabinet makers, medical workers. The UK list of required skills is extensive and the Philippines offersenglish speaking highly qualified hard working employees. Contact us today and make that first step to a highly motivated , quality skilled workforce.</p>
</section>

<section class="centers">
  <div class="center-head" style="top:3465px">
    <div class="eyebrow">Centers</div>
    <h2 class="title" style="font-size:34px;margin-top:10px">Archipel Manpower <span class="accent">Centers</span></h2>
    <div class="rule"></div>
    <p style="font-size:14.5px;color:#222;margin-top:20px">Our centres are highlighted in red dots on the map.</p>
  </div>
  <div class="map-area" role="img" aria-label="Map of the Philippines with recruitment centres marked in red dots"></div>
</section>

<footer class="site-footer">
  <h4 style="left:161px;top:78px">Quick Links</h4>
  <div class="foot-links" style="left:161px;top:120px">
    <span>Home</span><span>Articles</span><span>About</span><span>Training</span><span>Services</span><span>Contact Us</span>
  </div>
  <h4 style="left:441px;top:78px">Contact Details</h4>
  <div class="foot-contact" style="left:441px;top:118px;width:300px">
    <div><svg width="14" height="18" viewBox="0 0 14 18" fill="#fff"><path d="M7 0a7 7 0 0 0-7 7c0 5 7 11 7 11s7-6 7-11a7 7 0 0 0-7-7zm0 9.5A2.5 2.5 0 1 1 7 4.5a2.5 2.5 0 0 1 0 5z"/></svg><span>12 Ashdown Court, Fenwick Lane, Hullmere HU99 4ZZ United Kingdom</span></div>
    <div><svg width="14" height="14" viewBox="0 0 24 24" fill="#fff"><path d="M6.6 10.8a15 15 0 0 0 6.6 6.6l2.2-2.2c.3-.3.7-.4 1-.2 1.1.4 2.3.6 3.6.6.6 0 1 .4 1 1V20c0 .6-.4 1-1 1A17 17 0 0 1 3 4c0-.6.4-1 1-1h3.5c.6 0 1 .4 1 1 0 1.3.2 2.5.6 3.6.1.3 0 .7-.2 1z"/></svg><span>07700 900461</span></div>
    <div><svg width="16" height="12" viewBox="0 0 16 12" fill="none" stroke="#fff" stroke-width="1.4"><rect x=".7" y=".7" width="14.6" height="10.6"/><path d="M.7.7l7.3 6 7.3-6"/></svg><span>sales@archipelmanpower.example.com</span></div>
  </div>
  <h4 style="left:800px;top:78px">Follow Us On:</h4>
  <div class="social" style="left:800px;top:118px" aria-label="Social media links"><span></span><span></span><span></span><span></span></div>
  <div class="abs" style="left:800px;top:168px;font-size:22px;font-weight:600;color:#fff">Archipel Manpower</div>
</footer>
<div class="copyright">© 2023 Archipel Manpower Ltd. All Rights Reserved</div>

</body>
</html>
```